Creation of a construction/bricklaying business website

Following the template format of "Halloway 7", the following content would need to be included:
1. Landing page with 3 tiles that go to their own pages.
- Landing page to include background photo and description of services offered.
2. 3 tiles to include:
a) "Contact Us For A Free Quote or Friendly Discussion" Form (middle tile)
b) Case Studies and Testimonials
c) Certifications and Professional Membership
- Design logo to be used from previous SketchNestle project. Example of logo attached below, please access full JPG files from our account.

Target Market(s)

Prospective clients seeking construction work (bricklaying speciality)

Industry/Entity Type

Residential Construction

Coding

Coded - Design and coding required

Number of Pages Required

4 page

Font styles to use
Sans Serif

Colors

Designer to choose colors to be used in the design.

Requirements
Must have
• Following the template format of "Halloway 7", the following content would need to be included:
• 1. Landing parent page with 3 tiles that go to the 3 child pages.
• - Landing page to include background photo and description of services offered.
• 2. 3 tiles to include:
• a) "Contact Us For A Free Quote or Friendly Discussion" Form (middle tile)
• b) Case Studies and Testimonials (first tile / left side)
• c) Certifications and Professional Memberships (third tile / right side) (This should include logos of the relevant organisations being displayed. Specifically GQT and the Pillar Seal GQT).
• - Design logo to be used from previous SketchNestle project. Example of logo attached below, please access full JPG files from our account.
Nice to have
• Sleek and modern feel.
• Approachable in terms of how people can contact the company for a quote.
• Traditional pictures to give credibility and comfort around choosing this company.
Should not have
• Cheesy pictures
• Over-complicated
• Simple to use
• Easy URL domain name

```html
<!DOCTYPE html>
<html lang="en">
<head>
<meta charset="utf-8">
<title>R.T. Harwell Construction Ltd</title>
<link href="https://fonts.googleapis.com/css2?family=Exo+2:wght@500;600;700&family=Nunito+Sans:wght@400;600;700&display=swap" rel="stylesheet">
<style>
:root{
  --blue:#1d5ba8;
  --ink:#1b1b1b;
  --grey-tile:#e6eaea;
  --grey-field:#edf0f0;
  --badge:#c4cacc;
  --btn:#5b5b5b;
  --white:#ffffff;
  --footer-text:#f1f1f1;
}
*{box-sizing:border-box;margin:0;padding:0}
html,body{width:954px;height:1200px;overflow:hidden;background:var(--white)}
body{position:relative;font-family:"Nunito Sans",sans-serif;color:var(--ink)}
.abs{position:absolute}

/* header */
.brand{left:128px;top:22px;color:var(--blue);font-family:"Exo 2",sans-serif;font-weight:700;line-height:1}
.brand .name{font-size:30px;letter-spacing:.5px}
.brand .sub{font-size:11px;letter-spacing:2.4px;margin-top:3px}
.contact-item{display:flex;align-items:center;gap:8px;font-size:11px;color:#555;line-height:1.55}
.icon-circle{width:30px;height:30px;border-radius:50%;background:var(--blue);display:flex;align-items:center;justify-content:center;flex:none}

/* nav */
.nav{left:0;top:82px;width:954px;height:37px;background:var(--blue);display:flex;align-items:center;padding-left:131px;gap:20px}
.nav a{font-family:"Exo 2",sans-serif;font-weight:600;font-size:12.5px;color:var(--white);text-decoration:none;letter-spacing:.2px}
.nav a.active{color:#0d1e36}

/* hero */
.hero{left:0;top:119px;width:954px;height:417px;background:linear-gradient(90deg,#6b3b2a 0%,#8a4a35 25%,#7a4130 45%,#9a5a42 60%,#5a2f22 72%,#8d4d37 85%,#6b3a2a 100%)}
.hero-shade{left:0;top:119px;width:954px;height:417px;background:linear-gradient(180deg,rgba(0,0,0,0) 55%,rgba(120,110,100,.45) 100%)}
.services{left:118px;top:221px;width:272px;height:166px;background:rgba(30,30,30,.78);color:var(--white);padding:9px 0 0 16px}
.services p{font-family:"Exo 2",sans-serif;font-weight:600;font-size:11.8px;line-height:14.5px;letter-spacing:.2px;white-space:nowrap}
.services ul{list-style:none;display:grid;grid-template-columns:137px 120px;row-gap:5px;margin-top:11px}
.services li{display:flex;align-items:center;gap:12px;font-family:"Exo 2",sans-serif;font-weight:600;font-size:13.8px;line-height:15.5px;min-height:22px}
.services li::before{content:"";width:11px;height:11px;border-radius:50%;background:radial-gradient(circle at 40% 40%,#ffffff 0,#dbe9f7 45%,#7fb0e2 100%);flex:none}

/* about */
.about-title{left:0;top:561px;width:954px;text-align:center;font-family:"Exo 2",sans-serif;font-weight:700;font-size:22px;color:var(--blue)}
.about-text{left:120px;top:601px;width:714px;text-align:center;font-size:12.3px;line-height:19px;color:var(--ink)}
.about-text p+p{margin-top:12px}

/* tiles */
.tile{top:718px;width:226px;height:242px;background:var(--grey-tile)}
.tile-head{height:34px;background:var(--blue);display:flex;align-items:center;gap:10px;padding-left:8px;color:var(--white);font-family:"Exo 2",sans-serif;font-weight:600;font-size:11.5px;line-height:1.3}
.btn{position:absolute;bottom:12px;left:6px;height:21px;padding:0 13px;background:var(--btn);color:var(--white);font-family:"Exo 2",sans-serif;font-weight:600;font-size:11.5px;display:flex;align-items:center}
.quote-box{position:absolute;left:6px;top:44px;width:214px;height:104px;background:#edf1f1;border:1px solid #dfe4e4;border-radius:5px;padding:8px 6px 0 16px;font-size:9.2px;line-height:15.3px;color:#222;white-space:nowrap}
.quote-mark{position:absolute;left:5px;top:1px;font-family:"Exo 2",sans-serif;font-size:20px;color:#b9bfc0}
.quote-box .first{padding-left:14px}
.avatar{position:absolute;left:20px;top:137px;width:52px;height:52px;border-radius:50%;border:3px solid var(--white);background:linear-gradient(135deg,#c99a72,#8a6a4d)}
.client{position:absolute;left:82px;top:168px;font-size:9px;font-weight:700;color:#333}
.field{position:absolute;left:10px;width:205px;height:25px;background:var(--grey-field);border:1px solid #dde2e2;display:flex;align-items:center;gap:9px;padding-left:8px;font-size:10.5px;color:#222}
.field.msg{height:63px;align-items:flex-start;padding-top:6px}
.cert-text{position:absolute;left:0;top:42px;width:226px;text-align:center;font-size:11px;line-height:18px;color:#222}
.badge{position:absolute;background:var(--badge);border-radius:3px}

/* footer */
.footer{left:0;top:1000px;width:954px;height:200px;background:linear-gradient(180deg,#3d4448 0%,#2f3635 50%,#1f2a1d 100%)}
.footer-brand{left:0;top:1027px;width:954px;text-align:center;color:var(--white);font-family:"Exo 2",sans-serif;font-weight:700;line-height:1}
.footer-brand .name{font-size:19px}
.footer-brand .sub{font-size:7px;letter-spacing:1.6px;margin-top:2px}
.f-item{display:flex;align-items:center;gap:10px;color:var(--footer-text);font-size:11px;line-height:17px}
.f-item .icon-circle{width:31px;height:31px}
.copyright{left:148px;top:1167px;color:var(--footer-text);font-size:11px}
.social{left:682px;top:1160px;display:flex;gap:8px}
.social span{width:24px;height:24px;border-radius:50%;background:var(--white);display:block}
</style>
</head>
<body>

<div class="abs brand" aria-label="R.T. Harwell Construction Ltd">
  <div class="name">R.T. Harwell</div>
  <div class="sub">CONSTRUCTION LTD</div>
</div>

<div class="abs contact-item" style="left:517px;top:32px">
  <span class="icon-circle"><svg width="16" height="12" viewBox="0 0 16 12"><rect x="0.5" y="0.5" width="15" height="11" rx="1" fill="none" stroke="#fff"/><path d="M1 1l7 6 7-6M1 11l5-4.5M15 11l-5-4.5" fill="none" stroke="#fff"/></svg></span>
  <div>Email Us On<br>info@rtharwellbuild.com</div>
</div>
<div class="abs contact-item" style="left:713px;top:32px">
  <span class="icon-circle"><svg width="14" height="14" viewBox="0 0 24 24"><path fill="#fff" d="M6.6 10.8a15.1 15.1 0 006.6 6.6l2.2-2.2c.3-.3.7-.4 1-.2 1.1.4 2.3.6 3.6.6.6 0 1 .4 1 1V20c0 .6-.4 1-1 1A17 17 0 013 4c0-.6.4-1 1-1h3.5c.6 0 1 .4 1 1 0 1.3.2 2.5.6 3.6.1.3 0 .7-.2 1z"/></svg></span>
  <div>Call Us On<br>123.555.0142</div>
</div>

<nav class="abs nav">
  <a class="active" href="#">Home</a>
  <a href="#">Case Studies &amp; Testimonials</a>
  <a href="#">Contact Us For A Free Quote</a>
  <a href="#">Certifications &amp; Professional Memberships</a>
</nav>

<div class="abs hero" role="img" aria-label="Photo of a red brick building with two arched stone doorways, lanterns and ivy-covered steps"></div>
<div class="abs hero-shade"></div>
<div class="abs services">
  <p>R.T. Harwell Construction Ltd is a<br>construction company that has expertise<br>and experience in the following areas</p>
  <ul>
    <li>Extensions</li><li>Garden walls</li>
    <li>New build /<br>New houses</li><li>Plastering</li>
    <li>Garden walls</li><li>Brickwork</li>
  </ul>
</div>

<h1 class="abs about-title">About Us</h1>
<div class="abs about-text">
  <p>We pride ourselves on attention to detail, pride in our completed project and client satisfaction. We believe in full transparency<br>and this is reflected in the jobs we quote for you. We break down each step with both labour and materials cost so you can see<br>exactly what you are paying for.</p>
  <p>Feel free to get in touch and we can talk through what you are looking to achieve.</p>
</div>

<section class="abs tile" style="left:128px">
  <div class="tile-head">
    <svg width="40" height="26" viewBox="0 0 40 26"><rect x="14" y="2" width="18" height="22" rx="1" fill="none" stroke="#fff" stroke-width="1.5"/><path d="M17 8h12M17 12h12M17 16h8" stroke="#fff"/><circle cx="26" cy="17" r="3" fill="none" stroke="#fff"/><ellipse cx="8" cy="15" rx="6" ry="4.5" fill="#fff"/><path d="M4 18l-2 4 5-3" fill="#fff"/></svg>
    <span>Case Studies and<br>Testimonials</span>
  </div>
  <div class="quote-box">
    <span class="quote-mark">&ldquo;</span>
    <span class="first">Lorem ipsum dolor sit amet conetuge</span><br>sed diay nibhdl tincidunt ut laoreet dolore<br>magam er vol wisi enim ad minim vni quis<br>nostrud exerci tationorem ipsum dolor sit<br>ametee sed diammmy nibh.
  </div>
  <div class="avatar" role="img" aria-label="Client portrait photo"></div>
  <div class="client">Mr.Owen Pritchard</div>
  <div class="btn">View All</div>
</section>

<section class="abs tile" style="left:364px">
  <div class="tile-head">
    <svg width="30" height="28" viewBox="0 0 30 28"><path d="M6 2h13l6 6v18H6z" fill="none" stroke="#fff" stroke-width="1.5"/><path d="M19 2v6h6M10 12h11M10 16h11M10 20h7" stroke="#fff" stroke-width="1.3" fill="none"/><path d="M2 20l3 4 5-8" stroke="#fff" stroke-width="1.8" fill="none"/></svg>
    <span>Contact Us For A<br>Free Quote</span>
  </div>
  <div class="field" style="top:43px"><svg width="10" height="10" viewBox="0 0 10 10"><circle cx="5" cy="3" r="2.5" fill="#1d5ba8"/><path d="M0 10a5 4 0 0110 0z" fill="#1d5ba8"/></svg>Your Name</div>
  <div class="field" style="top:73px"><svg width="11" height="8" viewBox="0 0 11 8"><rect width="11" height="8" fill="#1d5ba8"/><path d="M0 0l5.5 4.5L11 0" stroke="#fff" fill="none"/></svg>Email Address</div>
  <div class="field" style="top:103px"><svg width="10" height="10" viewBox="0 0 24 24"><path fill="#1d5ba8" d="M6.6 10.8a15.1 15.1 0 006.6 6.6l2.2-2.2c.3-.3.7-.4 1-.2 1.1.4 2.3.6 3.6.6.6 0 1 .4 1 1V20c0 .6-.4 1-1 1A17 17 0 013 4c0-.6.4-1 1-1h3.5c.6 0 1 .4 1 1 0 1.3.2 2.5.6 3.6.1.3 0 .7-.2 1z"/></svg>Phone</div>
  <div class="field msg" style="top:133px"><svg width="11" height="11" viewBox="0 0 12 12"><path d="M12 0L0 5l4 2 1 5 2-3 3 2z" fill="#1d5ba8"/></svg>Message</div>
  <div class="btn">Submit</div>
</section>

<section class="abs tile" style="left:599px">
  <div class="tile-head">
    <svg width="30" height="28" viewBox="0 0 30 28"><rect x="6" y="2" width="18" height="24" rx="1" fill="none" stroke="#fff" stroke-width="1.6"/><circle cx="15" cy="10" r="3" fill="#fff"/><path d="M10 16h10M10 20h10" stroke="#fff" stroke-width="1.4"/></svg>
    <span>Certifications and Professional<br>Memberships</span>
  </div>
  <div class="cert-text">Ut wisi enim ad minim veniam, quis nostrud<br>exerci tation ullamcorper suscipit.</div>
  <div class="badge" style="left:21px;top:93px;width:50px;height:85px" role="img" aria-label="GQT membership badge"></div>
  <div class="badge" style="left:79px;top:104px;width:40px;height:64px" role="img" aria-label="GQT quality badge"></div>
  <div class="badge" style="left:129px;top:104px;width:76px;height:38px" role="img" aria-label="Pillar Seal GQT badge"></div>
  <div class="badge" style="left:129px;top:151px;width:74px;height:12px" role="img" aria-label="Warranty scheme badge"></div>
  <div class="btn">Know More</div>
</section>

<footer>
  <div class="abs footer" role="img" aria-label="Dusk photo of a modern housing development with trees and lawn"></div>
  <div class="abs footer-brand" aria-label="R.T. Harwell Construction Ltd">
    <div class="name">R.T. Harwell</div>
    <div class="sub">CONSTRUCTION LTD</div>
  </div>
  <div class="abs f-item" style="left:147px;top:1085px">
    <span class="icon-circle"><svg width="12" height="16" viewBox="0 0 12 16"><path d="M6 0a6 6 0 00-6 6c0 4.5 6 10 6 10s6-5.5 6-10a6 6 0 00-6-6z" fill="#fff"/><circle cx="6" cy="6" r="2.2" fill="#1d5ba8"/></svg></span>
    <div>Street Name, City Name<br>State Zipcode</div>
  </div>
  <div class="abs f-item" style="left:403px;top:1085px">
    <span class="icon-circle"><svg width="14" height="14" viewBox="0 0 24 24"><path fill="#fff" d="M6.6 10.8a15.1 15.1 0 006.6 6.6l2.2-2.2c.3-.3.7-.4 1-.2 1.1.4 2.3.6 3.6.6.6 0 1 .4 1 1V20c0 .6-.4 1-1 1A17 17 0 013 4c0-.6.4-1 1-1h3.5c.6 0 1 .4 1 1 0 1.3.2 2.5.6 3.6.1.3 0 .7-.2 1z"/></svg></span>
    <div>Call Us On :<br>123.555.0142</div>
  </div>
  <div class="abs f-item" style="left:614px;top:1085px">
    <span class="icon-circle"><svg width="16" height="12" viewBox="0 0 16 12"><rect x="0.5" y="0.5" width="15" height="11" rx="1" fill="none" stroke="#fff"/><path d="M1 1l7 6 7-6" fill="none" stroke="#fff"/></svg></span>
    <div>Email<br>info@rtharwellbuild.com</div>
  </div>
  <div class="abs copyright">Copyright &copy;2018 R.T. Harwell Construction Ltd. All Rights Reserved.</div>
  <div class="abs social" aria-label="Social media links">
    <span></span><span></span><span></span><span></span>
  </div>
</footer>

</body>
</html>
```